New Alcoholic Spiked Seltzer Line

We need a can design for a line of low calorie alcoholic seltzer. This product is a sparkling water and vodka drink with no sugar added in a slim 12 oz can.

This is a lighter, healthier, alternative to the sugary ready-to-drinks on the market. The product contains only 3 ingredients: Vodka, Water and Natural Flavors. It has only 100 calories but still has 5% alcohol, so you don't need to sacrifice alcohol to cut calories.

This product also does not contain any preservatives.

We want this design to communicate the following objectives to the consumer and in this order:

1. Appetizing product
2.Low calorie
3.Communicate the type of beverage (Spiked Seltzer)

The brand name of the product is VELKA.

The flavor of the product needed to be used for the design is Mango-Orange.

Comparable products are:

www.brindlefizzworks.example/
https://www.quorvabubbles.example
https://pelnavo.example/

The designs should not infringe or copy the creative directions of the products mentionned above. They are only given so that you can better understand the type of product we are developing.

Target Market(s)

Young Professional women between the ages of 25 and 44

Industry/Entity Type

Product

Colors

Designer to choose colors to be used in the design.

Requirements
Must have
• Design extendibility, meaning it can be adapted for other flavors.
• This is a new category in the market we are targeting, so consumers must easily be able to identify what type of product this is.

```html
<!DOCTYPE html>
<html lang="en">
<head>
<meta charset="utf-8">
<title>VELKA Spiked Seltzer – Mango-Orange Can Label</title>
<link rel="stylesheet" href="https://fonts.googleapis.com/css2?family=Source+Sans+3:wght@300;400;600;700;900&display=swap">
<style>
  :root {
    --gold-light: #f7c531;
    --gold-mid: #f0ab22;
    --gold-deep: #d98a14;
    --maroon: #7a0d0d;
    --red: #d4101a;
    --ram-dark: #5c0808;
    --ink: #1b1b1b;
    --band: #151515;
    --band-text: #f4b630;
    --white: #ffffff;
  }

  * { box-sizing: border-box; margin: 0; padding: 0; }

  html, body {
    width: 818px;
    height: 1200px;
    overflow: hidden;
    background: var(--white);
  }

  .can-label {
    position: relative;
    width: 818px;
    height: 1200px;
    overflow: hidden;
    font-family: "Source Sans 3", sans-serif;
    background: linear-gradient(90deg, var(--gold-deep) 0%, var(--gold-mid) 18%, var(--gold-light) 50%, var(--gold-mid) 82%, var(--gold-deep) 100%);
  }

  .category {
    position: absolute;
    top: 255px;
    left: 0;
    width: 100%;
    text-align: center;
    color: var(--maroon);
  }

  .category__title {
    font-size: 62px;
    font-weight: 400;
    line-height: 1;
    letter-spacing: 0.5px;
  }

  .category__subtitle {
    margin-top: 6px;
    font-size: 30px;
    font-weight: 600;
    color: var(--red);
    letter-spacing: 0.3px;
  }

  .mascot {
    position: absolute;
    top: 390px;
    left: 189px;
    width: 440px;
    height: 240px;
  }

  .brand-name {
    position: absolute;
    top: 640px;
    left: 0;
    width: 100%;
    text-align: center;
    font-size: 210px;
    font-weight: 900;
    line-height: 1;
    color: var(--red);
    letter-spacing: 4px;
  }

  .flavor {
    position: absolute;
    top: 920px;
    left: 0;
    width: 100%;
    text-align: center;
    font-size: 40px;
    font-weight: 300;
    color: var(--ink);
    letter-spacing: 0.5px;
  }

  .ingredients {
    position: absolute;
    top: 978px;
    left: 0;
    width: 100%;
    text-align: center;
    font-size: 34px;
    font-weight: 300;
    color: var(--white);
  }

  .base-band {
    position: absolute;
    left: 0;
    bottom: 0;
    width: 100%;
    height: 140px;
    background: var(--band);
    display: flex;
    align-items: center;
    justify-content: center;
  }

  .base-band__facts {
    font-size: 38px;
    font-weight: 400;
    color: var(--band-text);
    letter-spacing: 0.3px;
  }
</style>
</head>
<body>
  <main class="can-label">
    <header class="category">
      <h1 class="category__title">Spiked Seltzer</h1>
      <p class="category__subtitle">low calorie alcoholic seltzer</p>
    </header>

    <svg class="mascot" viewBox="0 0 440 240" role="img" aria-label="Illustrated ram head with curled horns, brand mascot">
      <defs>
        <radialGradient id="mascotTone" cx="50%" cy="45%" r="60%">
          <stop offset="0%" stop-color="#3a0a0a"/>
          <stop offset="100%" stop-color="#7a0d0d"/>
        </radialGradient>
      </defs>
      <rect x="0" y="0" width="440" height="240" rx="24" fill="url(#mascotTone)"/>
    </svg>

    <p class="brand-name">VELKA</p>

    <p class="flavor">MANGO-ORANGE</p>
    <p class="ingredients">Vodka, Water and Natural Flavors</p>

    <footer class="base-band">
      <p class="base-band__facts">5% alcohol - 100 calories</p>
    </footer>
  </main>
</body>
</html>
```